We are a recruitment company based in Norwich/Cambridge England.
I have included our company logo which we want to remain the same.

What we are looking for is a new creative Business card which will really stand out!!

Contact Information for Business Card

Harriet Dunmore
email: Harriet@plavex.co.uk
Address: Brackwell House
Fenmoor Enterprise Park
Partridge Way
Norwich
QB9 3KX
Tel:01632 960418

```html
<!DOCTYPE html>
<html lang="en">
<head>
<meta charset="utf-8">
<title>Plavex business card</title>
<link rel="stylesheet" href="https://fonts.googleapis.com/css2?family=Arimo:wght@400;700&display=swap">
<style>
  :root {
    --stage: #2a2a2c;
    --card-grey: #8c878e;
    --card-white: #ffffff;
    --accent-green: #7cc242;
    --ink-light: #ffffff;
    --brand-grey: #807b82;
  }
  html, body {
    margin: 0;
    padding: 0;
    overflow: hidden;
  }
  body {
    width: 1200px;
    height: 880px;
    background: var(--stage);
    position: relative;
    font-family: "Arimo", Arial, sans-serif;
  }
  .card {
    position: absolute;
    width: 540px;
    height: 310px;
    border-radius: 22px;
    overflow: hidden;
    box-shadow: 0 10px 30px rgba(0,0,0,0.45);
  }
  .card-front {
    left: 90px;
    top: 100px;
    background: var(--card-grey);
    display: flex;
    align-items: center;
    justify-content: center;
  }
  .card-back {
    left: 570px;
    top: 470px;
    background: var(--card-grey);
  }
  .brand {
    display: flex;
    align-items: center;
    gap: 14px;
    font-weight: 700;
    letter-spacing: -0.5px;
  }
  .brand-dot {
    border-radius: 50%;
    flex: none;
  }
  .card-front .brand { color: var(--ink-light); font-size: 60px; }
  .card-front .brand-dot { width: 40px; height: 40px; background: var(--ink-light); }
  .back-shape {
    position: absolute;
    inset: 0;
  }
  .card-back .brand {
    position: absolute;
    left: 52px;
    top: 128px;
    color: var(--accent-green);
    font-size: 46px;
  }
  .card-back .brand-dot { width: 30px; height: 30px; background: var(--brand-grey); }
  .contact {
    position: absolute;
    left: 345px;
    top: 34px;
    color: var(--ink-light);
    font-size: 12.5px;
    line-height: 1.35;
  }
  .contact-name {
    font-weight: 700;
    font-size: 19px;
    margin: 0;
  }
  .contact-role {
    margin: 0 0 18px;
    font-size: 13px;
  }
  .contact-address {
    margin: 0 0 14px;
    font-style: normal;
  }
  .contact-list {
    list-style: none;
    margin: 0;
    padding: 0;
  }
  .contact-list li {
    display: flex;
    align-items: center;
    gap: 8px;
    margin-bottom: 5px;
  }
  .contact-icon {
    width: 18px;
    height: 18px;
    flex: none;
  }
</style>
</head>
<body>
  <section class="card card-front" aria-label="Card front">
    <div class="brand"><span class="brand-dot"></span>Plavex</div>
  </section>

  <section class="card card-back" aria-label="Card back">
    <svg class="back-shape" viewBox="0 0 540 310" preserveAspectRatio="none" aria-hidden="true">
      <path d="M0,0 H255 Q425,150 325,310 H0 Z" fill="var(--accent-green)"/>
      <path d="M0,0 H255 Q395,150 303,310 H0 Z" fill="var(--card-white)"/>
    </svg>

    <div class="brand"><span class="brand-dot"></span>Plavex</div>

    <div class="contact">
      <p class="contact-name">Harriet Dunmore</p>
      <p class="contact-role">CEO</p>
      <address class="contact-address">
        Brackwell House<br>
        Fenmoor Enterprise Park<br>
        Partridge Way<br>
        Norwich QB9 3KX
      </address>
      <ul class="contact-list">
        <li>
          <svg class="contact-icon" viewBox="0 0 18 18" aria-hidden="true">
            <circle cx="9" cy="9" r="8" fill="none" stroke="#fff" stroke-width="1.2"/>
            <rect x="6.3" y="4.5" width="5.4" height="9" rx="1" fill="none" stroke="#fff" stroke-width="1.1"/>
          </svg>
          01632 960418
        </li>
        <li>
          <svg class="contact-icon" viewBox="0 0 18 18" aria-hidden="true">
            <circle cx="9" cy="9" r="8" fill="none" stroke="#fff" stroke-width="1.2"/>
            <rect x="4.8" y="6" width="8.4" height="6" fill="none" stroke="#fff" stroke-width="1.1"/>
            <path d="M4.8,6 L9,9.5 L13.2,6" fill="none" stroke="#fff" stroke-width="1.1"/>
          </svg>
          Harriet@plavex.co.uk
        </li>
        <li>
          <svg class="contact-icon" viewBox="0 0 18 18" aria-hidden="true">
            <circle cx="9" cy="9" r="8" fill="none" stroke="#fff" stroke-width="1.2"/>
            <circle cx="9" cy="9" r="4.5" fill="none" stroke="#fff" stroke-width="1"/>
            <path d="M4.5,9 H13.5 M9,4.5 V13.5" stroke="#fff" stroke-width="1"/>
          </svg>
          www.plavex.co.uk
        </li>
      </ul>
    </div>
  </section>
</body>
</html>
```